Marwick Law Letterhead

We need a new letterhead design for a Law Firm. The address for the law firm is 1475 Calloway Street, Suite 210, Houston, Texas 77041. Phone Number: 832-361-9027; Fax Number: 832-614-7359. The logo is uploaded to the project.

```html
<!DOCTYPE html>
<html lang="en">
<head>
<meta charset="utf-8">
<title>Marwick Law Letterhead</title>
<link href="https://fonts.googleapis.com/css2?family=Montserrat:wght@400;500&display=swap" rel="stylesheet">
<style>
  :root {
    --navy: #0f2452;
    --red: #d71a22;
    --red-deep: #8e0a14;
    --ink: #2b2b2b;
    --paper: #ffffff;
    --backdrop: #e9e9e9;
  }
  * { margin: 0; padding: 0; box-sizing: border-box; }
  html, body {
    width: 1154px;
    height: 1200px;
    overflow: hidden;
    background: var(--backdrop);
    font-family: "Montserrat", Arial, sans-serif;
  }
  .letterhead {
    position: absolute;
    left: 167px;
    top: 27px;
    width: 820px;
    height: 1146px;
    background: var(--paper);
    overflow: hidden;
  }
  .brand {
    position: absolute;
    left: 32px;
    top: 78px;
    display: flex;
    align-items: center;
    gap: 12px;
  }
  .brand-mark {
    width: 40px;
    height: 40px;
    background: var(--navy);
  }
  .brand-name {
    font-size: 32px;
    font-weight: 500;
    color: var(--navy);
  }
  .recipient {
    position: absolute;
    left: 30px;
    top: 257px;
    font-size: 13.6px;
    line-height: 20.4px;
    font-style: normal;
    color: #222;
  }
  .letter-body {
    position: absolute;
    left: 32px;
    top: 341px;
    width: 760px;
    font-size: 13.6px;
    line-height: 20.4px;
    color: var(--ink);
  }
  .letter-body p {
    text-align: justify;
    hyphens: auto;
    margin-bottom: 20.4px;
  }
  .closing {
    position: absolute;
    left: 30px;
    top: 827px;
    font-size: 17px;
    color: #222;
  }
  .signature {
    position: absolute;
    left: 29px;
    top: 860px;
    width: 92px;
    height: 24px;
    background: linear-gradient(90deg, #d9d9d9, #eeeeee);
    border-radius: 3px;
  }
  .footer-rule {
    position: absolute;
    left: 0;
    top: 944px;
    width: 820px;
    height: 10px;
    background: var(--navy);
  }
  .footer-band {
    position: absolute;
    left: 0;
    top: 960px;
    width: 820px;
    height: 186px;
    background: linear-gradient(180deg, var(--red), var(--red-deep));
  }
  .contact {
    position: absolute;
    left: 44px;
    top: 1009px;
    color: #fff;
    font-size: 14px;
    line-height: 17.7px;
  }
  .contact-address { margin-bottom: 9px; }
  .contact-line {
    display: flex;
    align-items: center;
    gap: 10px;
  }
  .contact-line svg { width: 11px; height: 11px; }
</style>
</head>
<body>
  <main class="letterhead">
    <header class="brand">
      <span class="brand-mark"></span>
      <span class="brand-name">Marwick Law</span>
    </header>

    <address class="recipient">
      Mr/s<br>
      First Name and Last Name<br>
      Company Name<br>
      Address
    </address>

    <section class="letter-body">
      <p>Lorem ipsum dolor sit amet,consectetur adipiscing sed do eiusmod tempor incididunt laboreet dolore magna aliqua.Ut enim ad minim.veniam, quis nostrud exercitation ullamco laboris nisi ut aliquip exea commodo consequat.Lorem ipsum dolor sit amet,consectetur adipiscing sed do eiusmod tempor incididunt.labore et dolore magna aliqua. Ut enim</p>
      <p>Lorem ipsum dolor sit amet, consectetur adipiscing sed do eiusmod tempor incididunt labore et dolore magna aliqua. Ut enim ad minim veniam, quis nostrud exercitation ullamco laboris nisi ut aliquip exea commodo consequat.Duis aute irure dolor in reprehenderit in voluptate velit esse cillum irure dolor in reprehenderit in voluptate velit esse irure</p>
      <p>Lorem ipsum dolor sit amet, consectetur adipiscing sed do eiusmod tempor incididunt labore et dolore magna aliqua. consequat. Duis aute irure dolor in.reprehenderit in voluptate velit esse cillum dolore eu fugiat nulla pariatur. Excepteur sint occaecat cupidatat non proident, sunt in culpa qui officia deserunt mollit,</p>
      <p>Lorem ipsum dolor sit amet, consectetur adipiscing sed do eiusmod tempor incididunt labore et dolore magna aliqua. Ut enim Lorem ipsum dolor sit amet, consectetur adipiscing sed do eiusmod tempor incididunt labore et dolore magna aliqua. Ut enim Lorem ipsum aliqua.ipsum</p>
      <p>Lorem ipsum dolor sit amet, consectetur adipiscing sed do eiusmod tempor incididunt labore et dolore magna aliqua. Ut enim ad minim veniam, quis nostrud exercitation ullamco laboris nisi ut aliquip exea commodo consequat.Duis aute irure dolor in reprehenderit in voluptate velit esse cillum irure dolor in reprehenderit in voluptate velit esse irure</p>
    </section>

    <div class="closing">Regards</div>
    <div class="signature" role="img" aria-label="Handwritten signature of the sender"></div>

    <div class="footer-rule"></div>
    <div class="footer-band"></div>

    <footer class="contact">
      <div class="contact-address">1475 Calloway Street,<br>Suite 210, Houston,<br>Texas 77041</div>
      <div class="contact-line">
        <svg viewBox="0 0 12 12" aria-label="Phone"><path fill="#fff" d="M2.3 1 L4.2 1 L5 3.4 L3.8 4.3 C4.4 5.7 5.6 6.9 7 7.6 L8 6.4 L11 7.3 L11 9.3 C11 10.2 10.3 11 9.4 11 C5 10.7 1.3 7 1 2.6 C1 1.7 1.5 1 2.3 1 Z"/></svg>
        <span>832-361-9027</span>
      </div>
      <div class="contact-line">
        <svg viewBox="0 0 12 12" aria-label="Fax"><path fill="#fff" d="M3 1 H9 V4 H3 Z M1 4.5 H11 V9 H9 V11 H3 V9 H1 Z M4 8 V10 H8 V8 Z"/></svg>
        <span>832-614-7359</span>
      </div>
    </footer>
  </main>
</body>
</html>
```